Medical Billing Company Needs a Business Card Design

We need a business card design for a Florida based medical billing company called 'Clinicians Keystone Solutions'. We specialize in providing revenue cycle management services to physician and therapist offices (we're basically their back-office processing partner for providing billing software, claims submissions, A/R follow-up and patient statements & collections. Our logo is red and blue-ish, so make sure that whatever other elements are used will match appropriately. Our current business card design has a too small font size. I'd like to project an image that shows we are modern & reliable. On a side note, I'm planning on using ZUB for printing these cards.

Target Market(s)

Office managers, physicians, therapists

Industry/Entity Type

Printing

Requirements
Must have
• Logo
Name of Employee
Phone
Fax
E-mail
Website

```html
<!DOCTYPE html>
<html lang="en">
<head>
<meta charset="utf-8">
<title>Clinicians Keystone – Business Card</title>
<link rel="stylesheet" href="https://fonts.googleapis.com/css2?family=Open+Sans:wght@400;600;700&display=swap">
<style>
  :root {
    --navy: #2b2f7a;
    --band: #3d3f95;
    --band-light: #5557b0;
    --red: #a3232a;
    --red-deep: #8e1a21;
    --red-glow: #c0454b;
    --ink: #2f3140;
    --white: #ffffff;
    --backdrop: #ecebe8;
  }
  * { margin: 0; padding: 0; box-sizing: border-box; }
  html, body {
    width: 1200px; height: 720px; overflow: hidden;
    background: var(--backdrop);
    font-family: "Open Sans", Arial, sans-serif;
  }
  .canvas {
    width: 1200px; height: 720px;
    display: flex; align-items: center; justify-content: center; gap: 40px;
  }
  .card {
    position: relative;
    width: 540px; height: 309px;
    overflow: hidden;
    box-shadow: 0 6px 18px rgba(0,0,0,0.18);
  }

  /* Front face */
  .card-front { background: var(--white); }
  .wave { position: absolute; left: 0; top: 0; width: 540px; height: 309px; }
  .brand-name {
    position: absolute; top: 34px; left: 0; right: 0;
    text-align: center;
    font-size: 27px; font-weight: 600; letter-spacing: 2px;
    color: var(--navy);
  }
  .contact-list {
    position: absolute; top: 112px; left: 52px;
    list-style: none;
    font-size: 13.5px; color: var(--ink); line-height: 21px;
  }
  .contact-list li { display: flex; align-items: center; gap: 8px; }
  .contact-list svg { width: 12px; height: 12px; flex: none; }
  .address {
    position: absolute; top: 112px; left: 322px;
    padding-left: 12px; border-left: 1px solid #c9c9d3;
    font-size: 12.5px; line-height: 17px; color: var(--ink);
    font-style: normal;
  }
  .employee {
    position: absolute; right: 24px; top: 262px;
    color: var(--white); font-size: 16px; font-weight: 700;
    white-space: nowrap;
  }
  .employee .title { font-size: 11.5px; font-weight: 400; }

  /* Back face */
  .card-back {
    background: radial-gradient(circle at 52% 48%, var(--red-glow) 0%, var(--red) 45%, var(--red-deep) 100%);
    color: var(--white);
  }
  .tagline {
    position: absolute; top: 30px; left: 0; right: 0; text-align: center;
    font-size: 14px; font-weight: 600; letter-spacing: 1.6px;
  }
  .back-name {
    position: absolute; top: 128px; left: 0; right: 0; text-align: center;
    font-size: 30px; font-weight: 600; letter-spacing: 2px;
  }
  .back-web {
    position: absolute; bottom: 34px; left: 0; right: 0; text-align: center;
    font-size: 14px; letter-spacing: 3px;
  }
</style>
</head>
<body>
<main class="canvas">

  <section class="card card-front" aria-label="Business card front">
    <svg class="wave" viewBox="0 0 540 309" aria-hidden="true">
      <path d="M0,200 C100,285 300,250 540,140 L540,309 L0,309 Z" fill="var(--red)"/>
      <path d="M0,207 C100,292 300,257 540,147" fill="none" stroke="var(--white)" stroke-width="3"/>
      <path d="M0,212 C100,297 300,262 540,152 L540,309 L0,309 Z" fill="var(--band)"/>
      <path d="M0,270 C120,305 250,300 380,309 L0,309 Z" fill="var(--band-light)" opacity="0.5"/>
    </svg>

    <h1 class="brand-name">CLINICIANS KEYSTONE</h1>

    <ul class="contact-list">
      <li>
        <svg viewBox="0 0 12 12"><circle cx="6" cy="6" r="6" fill="var(--navy)"/><path d="M4 3.2 L5 3 L5.6 4.6 L5 5.1 Q5.6 6.5 6.9 7 L7.4 6.4 L9 7 L8.8 8 Q6.5 8.5 4.5 6.5 Q3.4 5 4 3.2Z" fill="var(--white)"/></svg>
        555-310-2468
      </li>
      <li>
        <svg viewBox="0 0 12 12"><rect x="3.5" y="1" width="5" height="10" rx="1" fill="var(--navy)"/><rect x="4.3" y="2" width="3.4" height="6.5" fill="var(--white)"/></svg>
        555-310-2468
      </li>
      <li>
        <svg viewBox="0 0 12 12"><rect x="1" y="3" width="10" height="6.5" rx="1" fill="var(--navy)"/><path d="M1.5 3.5 L6 7 L10.5 3.5" fill="none" stroke="var(--white)" stroke-width="0.9"/></svg>
        info@clinicianskeystone.com
      </li>
      <li>
        <svg viewBox="0 0 12 12"><circle cx="6" cy="6" r="5.5" fill="var(--navy)"/><ellipse cx="6" cy="6" rx="2.2" ry="5" fill="none" stroke="var(--white)" stroke-width="0.8"/><path d="M1 6 H11" stroke="var(--white)" stroke-width="0.8"/></svg>
        www.clinicianskeystone.net
      </li>
    </ul>

    <address class="address">
      2780 SE Harbor Rd<br>
      Palm Grove, FL 34000
    </address>

    <p class="employee">Daniel Whitmore, <span class="title">CHBME, President</span></p>
  </section>

  <section class="card card-back" aria-label="Business card back">
    <p class="tagline">MEDICAL BILLING FOR HEALTHCARE PROFESSIONALS</p>
    <p class="back-name">CLINICIANS KEYSTONE</p>
    <p class="back-web">www.clinicianskeystone.net</p>
  </section>

</main>
</body>
</html>
```